IT Company requires new Business Card design.

Over the years we have had a few different business card designs. We are now due for new cards across the board for all staff. We felt this would be a good time to start fresh with a new design. Our traditional card simply had our details on the front, and a list of services on the back. We don't particularly need the list of services, we have had cards where the only thing on the rear of the card was our logo.
Feel free to be creative, we would like our tag line "Complete IT Management" to appear at some point, doesn't necessarily have to be with the logo.
I have attached samples and drafts of various previous cards we have used over the years.

```html
<!DOCTYPE html>
<html lang="en">
<head>
<meta charset="utf-8">
<title>Ridgeway Networks – Business Card</title>
<link rel="stylesheet" href="https://fonts.googleapis.com/css2?family=Open+Sans:wght@400;600;700;800&display=swap">
<style>
  :root {
    --bg: #e4e4e9;
    --card: #ffffff;
    --slate: #5f7280;
    --slate-dark: #4b5a66;
    --ink: #3a3f44;
    --rule: #c9ced3;
  }
  * { box-sizing: border-box; margin: 0; padding: 0; }
  html, body { width: 1200px; height: 987px; overflow: hidden; }
  body {
    background: var(--bg);
    font-family: "Open Sans", Arial, sans-serif;
    position: relative;
  }
  .card {
    position: absolute;
    width: 620px;
    height: 354px;
    background: var(--card);
    border-radius: 26px;
    box-shadow: 0 8px 24px rgba(60, 70, 80, 0.18);
    overflow: hidden;
  }
  .card--back { left: 520px; top: 70px; }
  .card--front { left: 60px; top: 560px; }

  .brand { display: flex; align-items: center; gap: 14px; color: var(--slate); font-weight: 800; }
  .brand__mark { background: var(--slate); flex: none; }
  .brand__name { line-height: 0.95; text-transform: uppercase; letter-spacing: 0.5px; }

  /* back */
  .card--back .brand { position: absolute; left: 120px; top: 100px; }
  .card--back .brand__mark { width: 72px; height: 72px; }
  .card--back .brand__name { font-size: 44px; }
  .card--back .web {
    position: absolute; left: 0; right: 0; top: 250px;
    text-align: center; font-size: 20px; letter-spacing: 1.5px; color: var(--ink);
  }

  /* front */
  .card--front .brand { position: absolute; left: 38px; top: 60px; }
  .card--front .brand__mark { width: 46px; height: 46px; }
  .card--front .brand__name { font-size: 27px; }
  .divider {
    position: absolute; left: 318px; top: 40px; width: 1px; height: 200px;
    background: linear-gradient(to bottom, transparent, var(--rule) 30%, var(--rule) 70%, transparent);
  }
  .contact { position: absolute; left: 340px; top: 38px; color: var(--ink); }
  .contact__name { font-size: 22px; font-weight: 700; color: var(--slate); line-height: 1.1; }
  .contact__role { font-size: 15px; margin-bottom: 10px; }
  .contact__list { list-style: none; }
  .contact__list li { display: flex; align-items: center; gap: 8px; font-size: 15px; line-height: 26px; }
  .contact__list svg { width: 15px; height: 15px; fill: var(--slate); flex: none; }

  .band-rule { position: absolute; left: 0; right: 0; height: 1px; background: var(--rule); }
  .band-rule--top { top: 252px; }
  .band-rule--bottom { top: 308px; }
  .address-band {
    position: absolute; left: 0; right: 0; top: 258px; height: 44px;
    background: var(--slate); color: #fff;
    display: flex; align-items: center; padding-left: 40px;
    font-size: 16px; letter-spacing: 0.3px;
  }
  .tagline {
    position: absolute; left: 40px; top: 318px;
    font-size: 15px; letter-spacing: 5px; color: var(--slate); text-transform: uppercase;
  }
</style>
</head>
<body>

<section class="card card--back" aria-label="Card back">
  <div class="brand">
    <span class="brand__mark"></span>
    <span class="brand__name">Ridgeway<br>Networks</span>
  </div>
  <p class="web">www.ridgewaynetworks.com.au</p>
</section>

<section class="card card--front" aria-label="Card front">
  <div class="brand">
    <span class="brand__mark"></span>
    <span class="brand__name">Ridgeway<br>Networks</span>
  </div>

  <div class="divider"></div>

  <div class="contact">
    <p class="contact__name">Marcus Hale</p>
    <p class="contact__role">Operation Manager</p>
    <ul class="contact__list">
      <li><svg viewBox="0 0 16 16"><path d="M3.5 1.5l2.5 0 1 3.5-1.6 1.2a8 8 0 0 0 4.4 4.4L11 9l3.5 1v2.5c0 1-.8 1.8-1.8 1.6A12 12 0 0 1 1.9 3.3c-.2-1 .6-1.8 1.6-1.8z"/></svg>08 5550 1842</li>
      <li><svg viewBox="0 0 16 16"><path d="M4.5 1h7a1 1 0 0 1 1 1v12a1 1 0 0 1-1 1h-7a1 1 0 0 1-1-1V2a1 1 0 0 1 1-1zm.5 2v8h6V3zm3 9.2a.9.9 0 1 0 0 1.8.9.9 0 0 0 0-1.8z"/></svg>0400 555 718</li>
      <li><svg viewBox="0 0 16 16"><path d="M4 1h6l2 2v3h1.5A1.5 1.5 0 0 1 15 7.5V12h-3v3H4v-3H1V7.5A1.5 1.5 0 0 1 2.5 6H4zm1 1v4h6V3.5L9.5 2zm0 8v4h6v-4z"/></svg>08 5550 1842</li>
      <li><svg viewBox="0 0 16 16"><path d="M1 3h14v10H1zm1.5 1.2v.4L8 8.6l5.5-4V4.2zm0 2v5.3h11V6.2L8 10.2z"/></svg>marcus@ridgewaynetworks.com.au</li>
      <li><svg viewBox="0 0 16 16"><path d="M8 1a7 7 0 1 0 0 14A7 7 0 0 0 8 1zm-1 1.6V5H4.3A5.5 5.5 0 0 1 7 2.6zm2 0A5.5 5.5 0 0 1 11.7 5H9zM3.7 6.5H7v3H3.7a5.5 5.5 0 0 1 0-3zm5.3 0h3.3a5.5 5.5 0 0 1 0 3H9zM4.3 11H7v2.4A5.5 5.5 0 0 1 4.3 11zM9 11h2.7A5.5 5.5 0 0 1 9 13.4z"/></svg>www.ridgewaynetworks.com.au</li>
    </ul>
  </div>

  <div class="band-rule band-rule--top"></div>
  <p class="address-band">Unit 4 18 Corella Road, Bayview WA 6000</p>
  <div class="band-rule band-rule--bottom"></div>
  <p class="tagline">Complete IT Management</p>
</section>

</body>
</html>
```